VENTURE CAPITAL GROUP BUSINESS CARD DESIGN

Venture Capital Group based in SF looking for a bold business card design. No trendy colour explosion, 3D effects etc. Just "simple" optical effects. Works on your brain, keeps your eye focused and sticks to your mind.
Target Market(s)
Technology startups
Industry/Entity Type
Venture Capital
Contact Information for Business Card
DESMOND WHITLAKE
MANAGING PARTNER
187 FENWORTH ST SAN FRANCISCO, CA 94187
415.555.0142 O
415.555.0147 F
415.555.0193 C
desmond@veldtmoorcapital.ventures

```html
<!DOCTYPE html>
<html lang="en">
<head>
<meta charset="utf-8">
<title>Veldtmoor Capital Group — Business Card</title>
<link rel="stylesheet" href="https://fonts.googleapis.com/css2?family=Lora:wght@400&family=Saira+Semi+Condensed:wght@600&display=swap">
<style>
  :root {
    --stage: #d9d8d8;
    --card-dark: #1b1b1b;
    --card-light: #fbfbfb;
    --green: #1f8a3a;
    --green-light: #4cb848;
    --green-deep: #136b35;
    --silver: #9a9a9a;
    --silver-light: #d4d4d4;
    --ink: #555555;
    --muted: #8a8a8a;
    --white: #ffffff;
  }
  * { margin: 0; padding: 0; box-sizing: border-box; }
  html, body { width: 1200px; height: 1200px; overflow: hidden; }
  body { background: var(--stage); position: relative; font-family: "Lora", Georgia, serif; }

  .card { position: absolute; width: 715px; overflow: hidden; }
  .card-front { left: 243px; top: 116px; height: 422px; background: var(--card-dark); }
  .card-back { left: 243px; top: 644px; height: 418px; background: var(--card-light); }

  .front-disc {
    position: absolute; left: 273px; top: 85px; width: 168px; height: 168px; border-radius: 50%;
    background: radial-gradient(circle at 50% 40%, #3a3a3a, #111111 75%);
  }
  .front-wordmark {
    position: absolute; left: 0; right: 0; top: 268px; text-align: center; color: var(--green);
  }
  .front-wordmark .brand-name { font-size: 50px; letter-spacing: 1px; line-height: 1; text-transform: uppercase; }
  .front-wordmark .brand-sub { font-size: 14px; letter-spacing: 7px; margin-top: 6px; text-transform: uppercase; }

  .back-waves { position: absolute; inset: 0; }

  .holder { position: absolute; right: 30px; top: 48px; text-align: right; color: var(--white); }
  .holder-name { font-family: "Saira Semi Condensed", "Arial Narrow", sans-serif; font-weight: 600; font-size: 27px; line-height: 1; }
  .holder-title { font-size: 16px; margin-top: 8px; }

  .back-disc {
    position: absolute; left: 37px; top: 152px; width: 80px; height: 80px; border-radius: 50%;
    background: radial-gradient(circle at 45% 40%, #ffffff, #dedede 80%);
  }
  .back-wordmark { position: absolute; left: 170px; top: 158px; color: var(--green); }
  .back-wordmark .brand-name { font-size: 42px; line-height: 1; text-transform: uppercase; letter-spacing: 0.5px; }
  .back-wordmark .brand-sub { font-size: 13px; letter-spacing: 6.5px; margin-top: 2px; padding-left: 68px; text-transform: uppercase; }

  .contacts { position: absolute; top: 292px; list-style: none; color: var(--ink); font-size: 18px; }
  .contacts li { display: flex; align-items: center; height: 26px; }
  .contacts svg { width: 18px; height: 18px; margin-right: 16px; fill: var(--green-deep); flex: none; }
  .contacts-phones { left: 40px; }
  .contacts-web { left: 253px; }
</style>
</head>
<body>

<section class="card card-front" aria-label="Card front">
  <div class="front-disc"></div>
  <div class="front-wordmark">
    <div class="brand-name">Veldtmoor</div>
    <div class="brand-sub">Capital Group</div>
  </div>
</section>

<section class="card card-back" aria-label="Card back">
  <svg class="back-waves" viewBox="0 0 715 418" aria-hidden="true">
    <defs>
      <linearGradient id="band-green" x1="0" x2="1" y1="0" y2="0">
        <stop offset="0" stop-color="#4cb848"/>
        <stop offset="0.55" stop-color="#1f8a3a"/>
        <stop offset="1" stop-color="#136b35"/>
      </linearGradient>
      <linearGradient id="band-silver" x1="0" x2="1" y1="0" y2="0">
        <stop offset="0" stop-color="#e2e2e2"/>
        <stop offset="0.5" stop-color="#9a9a9a"/>
        <stop offset="1" stop-color="#b5b5b5"/>
      </linearGradient>
    </defs>
    <path d="M0,0 H715 V168 C620,176 545,150 465,104 C375,52 220,12 0,44 Z" fill="url(#band-green)"/>
    <path d="M0,70 C200,25 360,52 455,108 C545,160 625,184 715,180 V193 C615,200 530,174 440,124 C345,72 190,48 0,88 Z" fill="url(#band-silver)"/>
  </svg>

  <div class="holder">
    <div class="holder-name">Desmond Whitlake</div>
    <div class="holder-title">Managing Partner</div>
  </div>

  <div class="back-disc"></div>
  <div class="back-wordmark">
    <div class="brand-name">Veldtmoor</div>
    <div class="brand-sub">Capital Group</div>
  </div>

  <ul class="contacts contacts-phones">
    <li><svg viewBox="0 0 24 24"><path d="M3 8c0-2 4-4 9-4s9 2 9 4v2h-5V8H8v2H3zM6 11h12l2 9H4z"/></svg>415.555.0142</li>
    <li><svg viewBox="0 0 24 24"><path d="M7 3h10v5H7zM3 9h18v8h-4v4H7v-4H3zM9 14v5h6v-5z"/></svg>415.555.0147</li>
    <li><svg viewBox="0 0 24 24"><path d="M7 2h10a1 1 0 0 1 1 1v18a1 1 0 0 1-1 1H7a1 1 0 0 1-1-1V3a1 1 0 0 1 1-1zm1 3v13h8V5z"/></svg>415.555.0193</li>
  </ul>

  <ul class="contacts contacts-web">
    <li><svg viewBox="0 0 24 24"><path d="M2 5h20v14H2zm2 2v1l8 5 8-5V7l-8 5z"/></svg>desmond@veldtmoorcapital.ventures</li>
    <li><svg viewBox="0 0 24 24"><path d="M12 2a10 10 0 1 0 0 20 10 10 0 0 0 0-20zm-1 2.1V8H7.6A8 8 0 0 1 11 4.1zm2 0A8 8 0 0 1 16.4 8H13zM4.3 10H11v4H4.3a8 8 0 0 1 0-4zm8.7 0h6.7a8 8 0 0 1 0 4H13zm-5.4 6H11v3.9A8 8 0 0 1 7.6 16zm5.4 0h3.4a8 8 0 0 1-3.4 3.9z"/></svg>www.veldtmoorcapital.ventures</li>
    <li><svg viewBox="0 0 24 24"><path d="M12 2a7 7 0 0 0-7 7c0 5 7 13 7 13s7-8 7-13a7 7 0 0 0-7-7zm0 4a3 3 0 1 1 0 6 3 3 0 0 1 0-6z"/></svg>187 Fenworth St San Francisco, CA 94187</li>
  </ul>
</section>

</body>
</html>
```